Business card design needed

I would like a one sided black business card with the information provided above. Refer to my website www.brightvolleyracquets.com.au for an example of colors I have used for my site, would like to keep this consistent for my business cards also, I will upload my logo below.

I am a new small business that provides tennis customers with racquet re stringing, tennis strings and accessories.

Industry/Entity Type

Small Business

Contact Information for Business Card

Bright Volley Tennis

Owen Whitby
Managing Director

brightvolleyracquets@mailbox.example
www.brightvolleyracquets.com.au
0491 726 305

Racquet Restringing/Tennis Strings/Accessories

Requirements
Must have
• Must have my logo and card must be black

```html
<!DOCTYPE html>
<html lang="en">
<head>
<meta charset="utf-8">
<title>Bright Volley Tennis – Business Card</title>
<link rel="stylesheet" href="https://fonts.googleapis.com/css2?family=Open+Sans:ital,wght@0,400;0,600;0,700;1,700&display=swap">
<style>
  :root {
    --backdrop: #5a3a22;
    --card-black: #030505;
    --lime: #bcd631;
    --white: #ffffff;
    --ink: #111111;
    --divider: #6a6a6a;
  }
  * { box-sizing: border-box; margin: 0; padding: 0; }
  html, body {
    width: 1200px;
    height: 750px;
    overflow: hidden;
    background: var(--backdrop);
    font-family: "Open Sans", Arial, sans-serif;
  }
  .card {
    position: absolute;
    left: 75px;
    top: 75px;
    width: 1050px;
    height: 598px;
    border-radius: 40px;
    background: var(--card-black);
    overflow: hidden;
  }
  .brand {
    position: absolute;
    left: 35px;
    top: 250px;
    width: 470px;
    display: flex;
    align-items: center;
    justify-content: center;
    gap: 14px;
  }
  .brand-dot {
    width: 34px;
    height: 34px;
    border-radius: 50%;
    background: var(--lime);
    flex: none;
  }
  .brand-name {
    color: var(--lime);
    font-weight: 700;
    font-size: 36px;
    letter-spacing: 0.5px;
    white-space: nowrap;
  }
  .divider {
    position: absolute;
    left: 487px;
    top: 168px;
    width: 3px;
    height: 232px;
    background: linear-gradient(to bottom, transparent, var(--divider) 25%, var(--divider) 75%, transparent);
  }
  .details {
    position: absolute;
    left: 515px;
    top: 168px;
    color: var(--white);
  }
  .person-name {
    color: var(--lime);
    font-weight: 700;
    font-size: 33px;
    line-height: 1.1;
  }
  .person-title {
    color: var(--lime);
    font-weight: 400;
    font-size: 24px;
    line-height: 1.3;
    margin-bottom: 40px;
  }
  .contact-line {
    font-size: 22px;
    line-height: 35px;
    white-space: nowrap;
  }
  .contact-label {
    font-weight: 700;
    font-style: italic;
  }
  .services {
    position: absolute;
    left: 0;
    bottom: 0;
    width: 100%;
    height: 76px;
    background: var(--lime);
    display: flex;
    align-items: center;
    justify-content: center;
    gap: 10px;
    list-style: none;
    color: var(--ink);
    font-size: 24px;
  }
  .service::before {
    content: "";
    display: inline-block;
    width: 8px;
    height: 8px;
    background: var(--ink);
    margin-right: 8px;
    vertical-align: 5px;
  }
  .service + .service { margin-left: 4px; }
</style>
</head>
<body>
  <main class="card">
    <div class="brand">
      <span class="brand-dot"></span>
      <span class="brand-name">Bright Volley Tennis</span>
    </div>

    <div class="divider"></div>

    <section class="details">
      <h1 class="person-name">Owen Whitby</h1>
      <p class="person-title">Managing Director</p>
      <p class="contact-line"><span class="contact-label">phone</span> 0491 726 305</p>
      <p class="contact-line"><span class="contact-label">email</span> brightvolleyracquets@mailbox.example</p>
      <p class="contact-line"><span class="contact-label">web</span> www.brightvolleyracquets.com.au</p>
    </section>

    <ul class="services">
      <li class="service">Racquet Restringing</li>
      <li class="service">Tennis Strings</li>
      <li class="service">Accessories</li>
    </ul>
  </main>
</body>
</html>
```